Business card design for my company.
I would like the card's background colour to be black. You can also see our web site to get an idea of our brand. https://www.tmwhomecrafting.com.au/
- Name
- Email

```html
<!DOCTYPE html>
<html lang="en">
<head>
<meta charset="utf-8">
<title>TMW Home Crafting – Business Card</title>
<link rel="stylesheet" href="https://fonts.googleapis.com/css2?family=Roboto:wght@300;400;500;700&display=swap">
<style>
  :root {
    --page-bg: #f2f2f2;
    --card-front: #232327;
    --card-back: #1f1f1f;
    --brand-green: #1a9a48;
    --text-light: #ffffff;
    --text-soft: #f0f0f0;
    --mark-muted: #46464b;
    --divider: #8a8a8a;
  }
  * { margin: 0; padding: 0; box-sizing: border-box; }
  html, body {
    width: 1200px; height: 987px; overflow: hidden;
    background: var(--page-bg);
    font-family: "Roboto", Arial, sans-serif;
  }
  .canvas { position: relative; width: 1200px; height: 987px; }
  .card {
    position: absolute; left: 245px; width: 709px; height: 405px;
    border-radius: 34px; overflow: hidden;
  }
  .card--front { top: 68px; background: var(--card-front); }
  .card--back { top: 513px; background: var(--card-back); }

  .front-brand {
    position: absolute; left: 0; right: 0; top: 160px;
    display: flex; align-items: center; justify-content: center; gap: 14px;
  }
  .front-brand__square { width: 30px; height: 30px; background: var(--mark-muted); }
  .front-brand__name {
    font-weight: 500; font-size: 44px; color: var(--mark-muted); letter-spacing: 1px;
  }
  .front-web {
    position: absolute; left: 0; right: 0; top: 346px;
    text-align: center; font-size: 17px; color: var(--text-light); letter-spacing: 0.5px;
  }
  .accent { color: var(--brand-green); }

  .back-brand {
    position: absolute; left: 28px; width: 298px; top: 180px;
    display: flex; align-items: center; justify-content: center; gap: 12px;
  }
  .back-brand__square { width: 24px; height: 24px; background: var(--brand-green); }
  .back-brand__name { font-weight: 500; font-size: 29px; color: var(--text-light); }

  .divider {
    position: absolute; left: 355px; top: 83px; width: 1px; height: 240px;
    background: var(--divider);
  }
  .contact { position: absolute; left: 385px; top: 96px; color: var(--text-soft); }
  .contact__name { font-size: 33px; font-weight: 300; color: var(--text-light); line-height: 1; }
  .contact__name strong { font-weight: 700; color: var(--brand-green); }
  .contact__role { font-size: 17px; margin-top: 4px; letter-spacing: 0.4px; }
  .contact__address { font-size: 17px; line-height: 23px; margin-top: 18px; letter-spacing: 0.4px; }
  .contact__list { list-style: none; margin-top: 18px; }
  .contact__item {
    display: flex; align-items: center; gap: 10px;
    font-size: 17px; height: 23.5px; letter-spacing: 0.4px;
  }
  .contact__icon { width: 15px; height: 15px; flex: none; }
</style>
</head>
<body>
<main class="canvas">
  <section class="card card--front" aria-label="Card front">
    <div class="front-brand">
      <span class="front-brand__square"></span>
      <span class="front-brand__name">TMW Home Crafting</span>
    </div>
    <p class="front-web">www.<span class="accent">tmwhomecrafting</span>.com.au</p>
  </section>

  <section class="card card--back" aria-label="Card back">
    <div class="back-brand">
      <span class="back-brand__square"></span>
      <span class="back-brand__name">TMW Home Crafting</span>
    </div>
    <div class="divider"></div>
    <div class="contact">
      <h1 class="contact__name"><strong>Liam</strong> Hartley</h1>
      <p class="contact__role">General Manager</p>
      <p class="contact__address">Hobart, Tasmania,<br>Australia</p>
      <ul class="contact__list">
        <li class="contact__item">
          <svg class="contact__icon" viewBox="0 0 24 24" aria-hidden="true"><path fill="#1a9a48" d="M6.6 10.8a15.1 15.1 0 0 0 6.6 6.6l2.2-2.2c.3-.3.7-.4 1-.2 1.1.4 2.3.6 3.6.6.6 0 1 .4 1 1V20c0 .6-.4 1-1 1A17 17 0 0 1 3 4c0-.6.4-1 1-1h3.5c.6 0 1 .4 1 1 0 1.3.2 2.5.6 3.6.1.3 0 .7-.2 1z"/></svg>
          <span>0400 555 018</span>
        </li>
        <li class="contact__item">
          <svg class="contact__icon" viewBox="0 0 24 24" aria-hidden="true"><circle cx="12" cy="12" r="9.5" fill="none" stroke="#1a9a48" stroke-width="2"/><path d="M2.5 12h19M12 2.5c3 3 3 16 0 19M12 2.5c-3 3-3 16 0 19" fill="none" stroke="#1a9a48" stroke-width="1.6"/></svg>
          <span>www.<span class="accent">tmwhomecrafting</span>.com.au</span>
        </li>
        <li class="contact__item">
          <svg class="contact__icon" viewBox="0 0 24 24" aria-hidden="true"><rect x="2" y="5" width="20" height="14" rx="1.5" fill="#1a9a48"/><path d="M2.5 6l9.5 7 9.5-7" fill="none" stroke="#1f1f1f" stroke-width="1.6"/></svg>
          <span>info@<span class="accent">tmwhomecrafting</span>.com.au</span>
        </li>
      </ul>
    </div>
  </section>
</main>
</body>
</html>
```